Verodex business card

Business card for sustainable investment company called "Verodex". Verodex is an exchange platform selling carbon credits between buyers and sellers. Carbon Credits are an environmental commodity for reducing global carbon emissions.

the card should obviously have our logo and the theme should be sustainability/environment mixed with a trading platform.

Contact Information for Business Card

Logo, Name, Title, Phone, Email

Colors
0054AA
0677BA
7BADD7
CADEEF
E8F1F8
0094D4
00A9DD
6FCCEA
C7EBF8
E9F6FB
00AB8E
00BBA5
67D7C9
C6EFE9
E9F9F6
59FF00
82FF00
B8FF75
E3FFCB
F4FFEA

```html
<!DOCTYPE html>
<html lang="en">
<head>
<meta charset="utf-8">
<title>Verodex business card</title>
<link rel="stylesheet" href="https://fonts.googleapis.com/css2?family=Arimo:wght@400;700&display=swap">
<style>
  :root {
    --backdrop: #1f1f21;
    --navy: #1b2c48;
    --navy-deep: #15233b;
    --navy-tone: #22365a;
    --paper: #f4f4f2;
    --ink: #1b2c48;
    --accent-blue: #1d6fdc;
    --icon-blue: #2a7be4;
  }
  * { box-sizing: border-box; margin: 0; padding: 0; }
  html, body {
    width: 1200px; height: 874px; overflow: hidden;
    background: var(--backdrop);
    font-family: "Arimo", Arial, sans-serif;
  }
  .sheet {
    position: relative; width: 1200px; height: 874px;
    display: flex; flex-direction: column; align-items: center; justify-content: center; gap: 40px;
  }
  .card {
    position: relative; width: 560px; height: 320px;
    border-radius: 18px; overflow: hidden;
  }
  .card-back {
    background: var(--navy);
    display: flex; align-items: center; justify-content: center; gap: 18px;
  }
  .back-mark { width: 92px; height: 92px; background: var(--navy-deep); }
  .back-name {
    font-weight: 700; font-size: 44px; letter-spacing: 1px; color: var(--navy-tone);
  }
  .card-front { background: var(--paper); }
  .front-shapes { position: absolute; inset: 0; }
  .brand {
    position: absolute; left: 74px; top: 126px;
    display: flex; align-items: center; gap: 12px;
  }
  .brand-square { width: 30px; height: 30px; background: var(--ink); }
  .brand-name { font-weight: 700; font-size: 28px; letter-spacing: 0.5px; color: var(--ink); line-height: 1; }
  .person {
    position: absolute; right: 74px; top: 182px; text-align: right;
  }
  .person-name { font-weight: 700; font-size: 23px; color: var(--accent-blue); line-height: 1.1; }
  .person-title { font-weight: 700; font-size: 14px; color: var(--ink); margin-top: 3px; }
  .contact {
    position: absolute; right: 112px; top: 254px; text-align: right;
    font-size: 14.5px; color: var(--ink); line-height: 1.35;
  }
  .contact-row { display: flex; align-items: center; justify-content: flex-end; gap: 8px; }
  .contact-row svg { width: 12px; height: 12px; fill: var(--icon-blue); }
</style>
</head>
<body>
  <main class="sheet">
    <section class="card card-back" aria-label="Card back">
      <span class="back-mark"></span>
      <span class="back-name">VERODEX</span>
    </section>

    <section class="card card-front" aria-label="Card front">
      <svg class="front-shapes" viewBox="0 0 560 320" aria-hidden="true">
        <polygon points="0,62 110,62 52,116 66,250 0,250" fill="var(--navy)"/>
        <polygon points="560,150 560,320 538,320 520,206" fill="var(--navy)"/>
      </svg>

      <div class="brand">
        <span class="brand-square"></span>
        <span class="brand-name">VERODEX</span>
      </div>

      <div class="person">
        <div class="person-name">Aaron Whitfield</div>
        <div class="person-title">President</div>
      </div>

      <div class="contact">
        <div class="contact-row">(555) 3210-7846
          <svg viewBox="0 0 24 24"><path d="M6.6 10.8a15.1 15.1 0 0 0 6.6 6.6l2.2-2.2a1 1 0 0 1 1-.25 11.4 11.4 0 0 0 3.6.57 1 1 0 0 1 1 1V20a1 1 0 0 1-1 1A17 17 0 0 1 3 4a1 1 0 0 1 1-1h3.5a1 1 0 0 1 1 1c0 1.25.2 2.45.57 3.57a1 1 0 0 1-.25 1z"/></svg>
        </div>
        <div class="contact-row">info@verodex.com
          <svg viewBox="0 0 24 24"><path d="M2 5h20v14H2z"/><path d="M2 6l10 7.5L22 6" fill="none" stroke="#fff" stroke-width="1.6"/></svg>
        </div>
      </div>
    </section>
  </main>
</body>
</html>
```